Yacht, Boats, Watersports company needs a redesign of business card

Hello Designers!
We are a Boat dealership company that sells fun in the water, we sell boats, Yachts, Kayaks and also yacht WaterSport toys. We are looking to redesign our business cards in to something a little bit more sophisticated. in a way that we can make better use of our company colors. I'm attaching a zipped file containing the company 3 sets of company logo which one is an horizontal another one is a vertical and also a chromed 3d logo. Also is included two set of business cards that we use and also some designs that i think it's interesting. We use PMS 2026c Orange and PMS 7687C Blue. I would like to see at least two different options with the orange as accent and also using blue as an accent color. It's really important for the business cards to have a font option and size that is legible to most people. Our current website is wwww.coralpennant.com. Please visit if you want to have a better feeling of the Boat dealership
You can send Single sided or double side options. We are now using single sided but we may be open for a double side option if we really like the design.
Target Market(s)
Marine, boat sales, yacht sales, water toys sales/
Contact Information for Business Card
Name: Dale Whitcombe
Address: 212 North Fenwick Lane,
Harbor Point, FL 33091
Phone: 954-731-8842
Fax: 954:731-8843
Cell: 954-382-1490
Email: dw@coralpennant.com
Website: coralpennant.com
Requirements
Must have
- the current information of the business card provided.
logo
use the PMS Colors
Nice to have
- a touch of elegance and sophistication but simple
Should not have
- should not have any typography that is hard to read, the card should be simple but yet sophisticated.

```html
<!DOCTYPE html>
<html lang="en">
<head>
<meta charset="utf-8">
<title>Coral Pennant – Business Card</title>
<link rel="stylesheet" href="https://fonts.googleapis.com/css2?family=Orbitron:wght@700&family=Roboto:wght@400;500&display=swap">
<style>
  :root {
    --brand-orange: #f26430;
    --brand-blue: #0e487c;
    --ink: #3c3c3c;
    --rule: #c8c8c8;
    --paper: #ffffff;
    --backdrop: #a9a9a9;
  }
  * { margin: 0; padding: 0; box-sizing: border-box; }
  html, body { width: 1200px; height: 1200px; overflow: hidden; }
  body { background: var(--backdrop); position: relative; font-family: "Roboto", Arial, sans-serif; }

  .card {
    position: absolute;
    top: 303px;
    width: 367px;
    height: 594px;
    box-shadow: 3px 4px 6px rgba(0,0,0,0.45);
    overflow: hidden;
  }
  .card--front { left: 200px; }
  .card--back { left: 599px; background: var(--paper); }

  .front-split { position: absolute; inset: 0; width: 100%; height: 100%; }
  .front-name {
    position: absolute;
    left: 0; right: 0;
    top: 282px;
    text-align: center;
    font-family: "Orbitron", Arial, sans-serif;
    font-weight: 700;
    font-size: 25px;
    letter-spacing: 1px;
    color: var(--paper);
  }

  .brand-dot {
    position: absolute;
    left: 50%;
    top: 106px;
    width: 68px;
    height: 68px;
    margin-left: -34px;
    border: 7px solid var(--brand-orange);
    border-radius: 50%;
  }
  .brand-name {
    position: absolute;
    left: 0; right: 0;
    top: 186px;
    text-align: center;
    font-family: "Orbitron", Arial, sans-serif;
    font-weight: 700;
    font-size: 21px;
    letter-spacing: 3px;
    color: var(--brand-blue);
  }

  .person-name {
    position: absolute;
    left: 0; right: 0;
    top: 315px;
    text-align: center;
    font-family: "Orbitron", Arial, sans-serif;
    font-weight: 700;
    font-size: 19px;
    letter-spacing: 1px;
  }
  .person-name .first { color: var(--brand-blue); }
  .person-name .last { color: var(--brand-orange); margin-left: 10px; }

  .rule {
    position: absolute;
    left: 117px;
    width: 132px;
    height: 1px;
    background: var(--rule);
  }
  .rule--top { top: 353px; }
  .rule--bottom { top: 495px; }

  .contact-list {
    position: absolute;
    left: 0; right: 0;
    top: 366px;
    list-style: none;
    text-align: center;
    font-size: 17px;
    line-height: 21.5px;
    color: var(--ink);
  }
  .contact-list .label { color: var(--brand-blue); font-weight: 500; }
  .contact-list .site-name { color: var(--brand-blue); }

  .address {
    position: absolute;
    left: 0; right: 0;
    top: 506px;
    text-align: center;
    font-size: 17px;
    line-height: 21.5px;
    color: var(--ink);
    font-style: normal;
  }
</style>
</head>
<body>
  <section class="card card--front">
    <svg class="front-split" viewBox="0 0 367 594" preserveAspectRatio="none" aria-hidden="true">
      <rect width="367" height="594" fill="var(--brand-orange)"/>
      <polygon points="0,478 367,189 367,594 0,594" fill="var(--brand-blue)"/>
    </svg>
    <p class="front-name">CORAL PENNANT</p>
  </section>

  <section class="card card--back">
    <span class="brand-dot" aria-hidden="true"></span>
    <p class="brand-name">CORAL PENNANT</p>

    <h1 class="person-name"><span class="first">DALE</span><span class="last">WHITCOMBE</span></h1>
    <div class="rule rule--top"></div>

    <ul class="contact-list">
      <li><span class="label">P:</span> 954-731-8842</li>
      <li><span class="label">F:</span> 954:731-8843</li>
      <li><span class="label">M:</span> 954-382-1490</li>
      <li><span class="label">P:</span> dw@coralpennant.com</li>
      <li>www.<span class="site-name">coralpennant</span>.com</li>
    </ul>

    <div class="rule rule--bottom"></div>
    <address class="address">212 North Fenwick Lane<br>Harbor Point, FL 33091</address>
  </section>
</body>
</html>
```